Veterinary Pylon

My veterinary clinic is not clearly visible from the street and I want to place a Pylon next to my driveway. I want a modern, elegant straight Design, the Photo shows the sheduled place. One can see the clinic on our Homepage: www.tailbright-vethaus.at
The last pictures are examples for pylones I like

Target Market(s)

the passing cars often miss my entry...I want to show where to turn left

Colors
3276b5
33a6d7
00a990

Requirements
Must have
• High value, simple elegance, size: 250cm (high) x 100cm (width)
Nice to have
• Our Logo, arrow(?)

A special Text is not necessary but this will be an option:

Biegen sie hier ab und wir biegen es wieder hin!
Should not have
• Too much Color, the colors I have chosen are the possible colors but it‘s not necessary to use them.

```html
<!DOCTYPE html>
<html lang="en">
<head>
<meta charset="utf-8">
<title>Tailbright Vethaus – Pylon</title>
<link rel="stylesheet" href="https://fonts.googleapis.com/css2?family=Roboto:wght@400;700;900&display=swap">
<style>
  :root {
    --navy: #124a91;
    --sky: #2ebadd;
    --white: #ffffff;
    --sky-soft: #8fd3ea;
  }
  html, body {
    margin: 0;
    padding: 0;
    width: 1200px;
    height: 3000px;
    overflow: hidden;
    background: var(--white);
  }
  .pylon {
    position: relative;
    width: 1200px;
    height: 3000px;
    overflow: hidden;
    background: var(--white);
    font-family: "Roboto", Arial, sans-serif;
  }
  .hero-illustration {
    position: absolute;
    left: 245px;
    top: 64px;
    width: 740px;
    height: 443px;
    border-radius: 40px;
    background: linear-gradient(160deg, var(--sky-soft) 0%, var(--navy) 100%);
    opacity: 0.85;
  }
  .brand-name {
    position: absolute;
    left: 0;
    top: 612px;
    width: 1200px;
    text-align: center;
    color: var(--navy);
    font-weight: 900;
    line-height: 1;
    margin: 0;
  }
  .brand-name .line-main {
    display: block;
    font-size: 150px;
    letter-spacing: -2px;
  }
  .brand-name .line-sub {
    display: block;
    margin-top: 30px;
    font-size: 80px;
    letter-spacing: 14px;
  }
  .brand-rule {
    position: absolute;
    top: 908px;
    height: 8px;
    background: var(--navy);
  }
  .brand-rule.left { left: 212px; width: 188px; }
  .brand-rule.right { left: 798px; width: 186px; }
  .turn-arrow {
    position: absolute;
    left: 430px;
    top: 1070px;
    width: 370px;
    height: 285px;
  }
  .footer-waves {
    position: absolute;
    left: 0;
    top: 1400px;
    width: 1200px;
    height: 1600px;
  }
  .contact {
    position: absolute;
    left: 0;
    top: 1770px;
    width: 1200px;
    text-align: center;
    color: var(--white);
  }
  .contact-title {
    margin: 0 0 28px;
    font-size: 82px;
    font-weight: 700;
    line-height: 1;
  }
  .contact-line {
    margin: 0;
    font-size: 62px;
    font-weight: 400;
    line-height: 115px;
  }
  .footer-illustration {
    position: absolute;
    left: 291px;
    top: 2516px;
    width: 694px;
    height: 484px;
    border-radius: 40px 40px 0 0;
    background: linear-gradient(180deg, rgba(255,255,255,0.9) 0%, rgba(255,255,255,0.55) 100%);
  }
</style>
</head>
<body>
<main class="pylon">
  <div class="hero-illustration" role="img" aria-label="Illustration of a dog and a cat in front of a heart with a heartbeat line"></div>

  <h1 class="brand-name">
    <span class="line-main">TAILBRIGHT</span>
    <span class="line-sub">VETHAUS</span>
  </h1>

  <svg class="turn-arrow" viewBox="0 0 370 285" aria-label="Turn left here" role="img">
    <defs>
      <linearGradient id="arrowFade" x1="0" y1="0" x2="1" y2="0">
        <stop offset="0" stop-color="#1f72ad"/>
        <stop offset="1" stop-color="#2ebadd"/>
      </linearGradient>
    </defs>
    <path d="M368 128 H67 L153 42 V2 L10 142 L153 283 V243 L67 156 H368 Z" fill="url(#arrowFade)"/>
  </svg>

  <svg class="footer-waves" viewBox="0 0 1200 1600" preserveAspectRatio="none" aria-hidden="true">
    <path d="M0 7 C170 5 330 40 470 110 L0 330 Z" fill="var(--sky)"/>
    <path d="M0 324 C300 120 560 68 800 70 C960 72 1090 100 1200 132 V1600 H0 Z" fill="var(--navy)"/>
  </svg>

  <section class="contact">
    <h2 class="contact-title">TAILBRIGHT VETHAUS</h2>
    <p class="contact-line">Vethaus Birkenfeld Dorfstrasse 18</p>
    <p class="contact-line">8573 Birkenfeld on the Lahnbach</p>
    <p class="contact-line">Tel:&nbsp; +43 3100 48217</p>
    <p class="contact-line">Mail: office@tailbright-vethaus.at</p>
  </section>

  <div class="footer-illustration" role="img" aria-label="White silhouette illustration of a dog and a cat with a heartbeat line"></div>
</main>
</body>
</html>
```